Business Cards Design for the electrical wholesaler: clean bold dynamic :)

We need a business card design that would follow our latest brand guidelines. As an electrical wholesaler we want to bring a fresh look and feel into the industry. The design should be clean bold and dynamic. It should come alive with the renewed energy of our green colour. Our grey colour should keep things balanced and complement the notion of maturity and responsibility. We employ Lato as a corporate font however are not bound by this font and we’re open to interpretation here.

Target Market(s)

Electrical contractors

Industry/Entity Type

Business

Contact Information for Business Card

Logo
Name & Surname: Halyna Dorosh
Job Title: Director of Marketing
Email: halya.dorosh@quillmail.example
Cell phone: XXX.XXX.XXXX
Address: 20517 - 87 Ave. Edmonton, AB, Canada. T6K 4N8
Business Phone: 780.555.0184
Website: www.brovix.example

Font styles to use
Other font styles liked:
• Lato

Requirements
Must have
• Logo & website
Nice to have
• Brand elements - some of them you may find in the attached Brand Guidelines (e.g. three lines on the background signifying "W")

```html
<!DOCTYPE html>
<html lang="en">
<head>
<meta charset="utf-8">
<title>Brovix Business Card</title>
<link href="https://fonts.googleapis.com/css2?family=Lato:wght@400;700;900&display=swap" rel="stylesheet">
<style>
  :root {
    --backdrop: #8e9091;
    --card-grey: #505051;
    --card-grey-light: #5a5a5b;
    --brand-green: #8dc63f;
    --brand-green-dark: #6aa533;
    --brand-green-deep: #74b843;
    --ink-grey: #4b4b4c;
    --white: #ffffff;
  }
  html, body {
    margin: 0;
    padding: 0;
    width: 1200px;
    height: 1000px;
    overflow: hidden;
    background: var(--backdrop);
  }
  .stage { display: block; width: 1200px; height: 1000px; }
  .card-front-bg { fill: var(--card-grey); }
  .card-front-band { fill: var(--card-grey-light); }
  .accent { fill: var(--brand-green); }
  .accent-dark { fill: var(--brand-green-dark); }
  .card-back-bg { fill: var(--brand-green); }
  .name, .title, .contact, .address, .brand-name {
    font-family: "Lato", sans-serif;
  }
  .name { fill: var(--brand-green); font-size: 24px; font-weight: 700; }
  .title { fill: var(--brand-green); font-size: 20px; font-weight: 700; }
  .divider { fill: var(--brand-green); font-size: 22px; font-weight: 400; }
  .contact { fill: var(--brand-green); font-size: 16px; font-weight: 400; }
  .address { fill: var(--brand-green); font-size: 15px; font-weight: 400; }
  .brand-name-small { fill: var(--white); font-size: 30px; font-weight: 700; }
  .brand-dot-small { fill: var(--white); }
  .brand-name-large { fill: var(--ink-grey); font-size: 78px; font-weight: 700; }
  .brand-dot-large { fill: var(--white); }
</style>
</head>
<body>
<svg class="stage" viewBox="0 0 1200 1000" xmlns="http://www.w3.org/2000/svg">
  <defs>
    <linearGradient id="backDecorGradient" x1="0" y1="0" x2="1" y2="0">
      <stop offset="0" stop-color="#8dc63f" stop-opacity="0"/>
      <stop offset="1" stop-color="#74b843"/>
    </linearGradient>
    <clipPath id="frontClip"><rect width="560" height="320" rx="4"/></clipPath>
    <clipPath id="backClip"><rect width="560" height="320" rx="4"/></clipPath>
  </defs>

  <!-- Front: contact side -->
  <g class="card-front" transform="translate(320 150)">
    <g clip-path="url(#frontClip)">
      <rect class="card-front-bg" width="560" height="320"/>
      <polygon class="card-front-band" points="300,0 360,0 560,260 560,320 500,320 300,60" opacity="0.6"/>
      <polygon class="card-front-band" points="390,0 440,0 560,160 560,220" opacity="0.5"/>

      <text x="40" y="72"><tspan class="name">Halyna Dorosh</tspan><tspan class="divider" dx="14">|</tspan><tspan class="title" dx="14">Director of Marketing</tspan></text>

      <rect class="accent" x="180" y="86" width="380" height="10"/>
      <rect class="accent-dark" x="180" y="96" width="380" height="5"/>
      <path class="accent" d="M50 118 H230 V132 H57 A7 7 0 0 1 50 125 Z"/>

      <text class="contact" x="60" y="165">halya.dorosh@quillmail.example</text>
      <text class="contact" x="60" y="188">Work: 780.555.0184  |  Cell: 780.555.0239</text>
      <text class="contact" x="60" y="211">www.brovix.example</text>

      <path class="accent" d="M30 226 H236 A8 8 0 0 1 236 242 H30 Z"/>
      <rect class="accent" x="0" y="244" width="560" height="12"/>
      <rect class="accent-dark" x="0" y="256" width="560" height="5"/>

      <text class="address" x="525" y="230" text-anchor="end">20517 - 87 Ave.</text>
      <text class="address" x="525" y="296" text-anchor="end">Edmonton, AB, Canada. T6K 4N8</text>

      <circle class="brand-dot-small" cx="68" cy="289" r="10"/>
      <text class="brand-name brand-name-small" x="86" y="300">brovix</text>
    </g>
  </g>

  <!-- Back: brand side -->
  <g class="card-back" transform="translate(320 520)">
    <g clip-path="url(#backClip)">
      <rect class="card-back-bg" width="560" height="320"/>
      <rect x="250" y="0" width="310" height="320" fill="url(#backDecorGradient)" role="img" aria-label="Brand stripe decoration in green tones"/>
      <circle class="brand-dot-large" cx="140" cy="160" r="26"/>
      <text class="brand-name brand-name-large" x="182" y="186">brovix</text>
    </g>
  </g>
</svg>
</body>
</html>
```